Bauzaunplane für Weihnachtsmarkt
Zielgruppe
Endverbraucher, die den Weihnachtsmarkt besuchen / besuchen sollen.
Aufgabenstellung
Benötigt wird ein Entwurf für eine Bauzaunplane (B) 2,12m x (H) 1,72m. Diese wird auf einem Weihnachtsmarkt als Sichtblende eingesetzt.
Die Gestaltung soll Atmosphäre vermitteln und ggf. Bezug zu Nikolaus, Engeln und anderen Adventssysmbolen nehmen (Hinweis: Der Weihnachtsmann kommt ind er Bibel nicht vor!)
Der Claim" Wir wünschen Ihnen eine schöne Zeit auf dem Lindauer Adventsmarkt" soll in das Motiv integriert werden.
Das Banner wird anschließend im Digitaldruck 4/0 C produziert. gefordert ist abschließend eine druckfähige Vorlage mit ausreichender Auflösung (ca. 100dpi auf das Endformat) vorzugsweise PDF/X3 - ISOcoatedV2ECI.

```html
<!DOCTYPE html>
<html lang="de">
<head>
<meta charset="utf-8">
<title>Lindauer Adventsmarkt – Bauzaunplane</title>
<link rel="stylesheet" href="https://fonts.googleapis.com/css2?family=Pinyon+Script&family=Rye&display=swap">
<style>
  :root {
    --sky-dark: #6e0a10;
    --sky-mid: #a50d16;
    --sky-red: #e0101e;
    --glow-gold: #f3cf86;
    --house-gold: #c8913f;
    --snow-peach: #f4a77e;
    --snow-cream: #fbe3c6;
    --snow-white: #ffffff;
    --gold: #a8742a;
    --gold-light: #f5c552;
    --gold-dark: #8a5a1e;
    --market-red: #c0192b;
    --band-red: #d9111c;
  }
  * { margin: 0; padding: 0; box-sizing: border-box; }
  html, body { width: 1200px; height: 974px; overflow: hidden; background: var(--snow-white); }
  .banner { position: relative; width: 1200px; height: 974px; overflow: hidden; background: var(--snow-white); }
  .winter-sky {
    position: absolute; left: 0; top: 0; width: 1200px; height: 520px;
    background: linear-gradient(180deg, var(--sky-dark) 0%, var(--sky-mid) 35%, var(--sky-red) 72%, #e8402c 100%);
  }
  .village-glow {
    position: absolute; left: 170px; top: 120px; width: 860px; height: 300px;
    background:
      radial-gradient(ellipse 48% 55% at 50% 75%, var(--glow-gold) 0%, var(--house-gold) 45%, rgba(200,145,63,0.35) 75%, rgba(200,145,63,0) 100%);
  }
  .snow-hills { position: absolute; left: 0; top: 0; width: 1200px; height: 974px; }
  .claim {
    position: absolute; left: 0; width: 1200px; top: 518px; text-align: center;
    font-family: "Pinyon Script", cursive; font-size: 62px; color: var(--gold);
    line-height: 1;
  }
  .market-name {
    position: absolute; left: 0; width: 1200px; text-align: center;
    font-family: "Rye", serif; font-weight: 400; color: var(--market-red);
    text-shadow: 2px 2px 0 var(--snow-white), 4px 4px 0 var(--gold);
    line-height: 1;
  }
  .market-name--town { top: 614px; font-size: 116px; }
  .market-name--event { top: 738px; font-size: 104px; letter-spacing: 2px; }
  .gold-band {
    position: absolute; left: 0; top: 922px; width: 1200px; height: 22px;
    background: linear-gradient(90deg, var(--gold-dark), #d79a32 12%, var(--gold-dark) 22%, #d8a444 40%, var(--gold-light) 55%, #d8a444 72%, var(--gold-dark) 90%, #d79a32);
  }
  .red-rule { position: absolute; left: 0; top: 945px; width: 1200px; height: 4px; background: var(--band-red); }
  .red-band { position: absolute; left: 0; top: 953px; width: 1200px; height: 21px; background: var(--band-red); }
</style>
</head>
<body>
<main class="banner">
  <div class="winter-sky"></div>
  <div class="village-glow" role="img" aria-label="Verschneites goldenes Dorf mit Kirche, rauchenden Schornsteinen und geschmücktem Weihnachtsbaum unter rotem Himmel mit fallendem Schnee"></div>
  <svg class="snow-hills" viewBox="0 0 1200 974" aria-hidden="true">
    <path d="M0 380 C180 330 300 360 420 380 C620 410 820 330 1000 340 C1100 345 1160 360 1200 370 L1200 974 L0 974 Z" fill="#ec6a45" opacity="0.85"/>
    <path d="M0 410 C200 370 330 390 460 395 C700 400 900 350 1200 395 L1200 974 L0 974 Z" fill="var(--snow-peach)"/>
    <path d="M0 450 C220 400 420 385 620 388 C850 392 1050 420 1200 455 L1200 974 L0 974 Z" fill="var(--snow-cream)"/>
    <path d="M0 515 C260 440 460 415 640 418 C860 422 1060 460 1200 505 L1200 974 L0 974 Z" fill="var(--snow-white)"/>
  </svg>
  <p class="claim">Wir wünschen Ihnen eine schöne Zeit auf dem</p>
  <h1 class="market-name market-name--town">LINDAUER</h1>
  <h2 class="market-name market-name--event">ADVENTSMARKT</h2>
  <div class="gold-band"></div>
  <div class="red-rule"></div>
  <div class="red-band"></div>
</main>
</body>
</html>
```